Letterhead for Business Law Firm

We need a letter head for our firm based on the design we have settled on and it is attached. Our clients are small and large businesses around the world, and our letterhead is used typically for formal legal purposes such as demand letters (accusing the recipient of doing bad things) or responding to demand letters. It may also be sent to regulators and other government agencies. So this needs to be tasteful, but a little edgy as well - we try to convey that we are a firm that is different - businesses and investors come to us for creative, quick advice, typically in high stress circumstances, and for our ability to work through high conflict situations, and rapid paced engagements.

Target Market(s)

Lawyers, business executives, investors, government regulators who may receive letters from this firm on behalf of its clients.

Industry/Entity Type

Business

Requirements
Must have
• The design and the firm's contact information:
• Thornwell Law Firm, P.C.
• 1876 NE 57th Ave
• Portland, OR 97213
• phone: 971 555 0147
• fax: 971 555 0182
• in what placement and how depicted (e.g. a phone icon instead of the word "phone") I leave to your creative ideas.
Nice to have
• design and information can be placed at the top, bottom and/or sides of the letter, and the design should be for a standard letter size paper - and can have a separate design for the second page.

```html
<!DOCTYPE html>
<html lang="en">
<head>
<meta charset="utf-8">
<title>Thornwell Law Firm, P.C. — Letterhead</title>
<link href="https://fonts.googleapis.com/css2?family=Open+Sans:wght@300;400&display=swap" rel="stylesheet">
<style>
  :root {
    --paper: #ffffff;
    --ink: #1d171a;
    --teal: #3f7479;
    --footer-text: #f2f2f2;
  }
  * { box-sizing: border-box; margin: 0; padding: 0; }
  html, body { width: 1019px; height: 1200px; overflow: hidden; background: var(--paper); }
  .letterhead {
    position: relative;
    width: 1019px;
    height: 1200px;
    background: var(--paper);
    font-family: "Open Sans", Arial, sans-serif;
  }
  .brand {
    position: absolute;
    top: 72px;
    left: 0;
    width: 100%;
    display: flex;
    justify-content: center;
    align-items: center;
    gap: 22px;
  }
  .brand-square {
    width: 70px;
    height: 70px;
    background: var(--ink);
  }
  .brand-name {
    font-weight: 300;
    font-size: 62px;
    letter-spacing: 12px;
    color: var(--ink);
    line-height: 1;
  }
  .address-band {
    position: absolute;
    left: 0;
    top: 1111px;
    width: 100%;
    height: 35px;
    background: var(--teal);
    color: var(--footer-text);
    font-size: 14.5px;
    letter-spacing: 1.6px;
    display: flex;
    align-items: center;
    justify-content: center;
  }
  .contact-band {
    position: absolute;
    left: 0;
    top: 1146px;
    width: 100%;
    height: 54px;
    background: var(--ink);
    color: var(--footer-text);
    font-size: 15px;
    display: flex;
    align-items: center;
    justify-content: center;
    gap: 14px;
  }
  .contact-item { display: flex; align-items: center; gap: 5px; }
  .contact-item svg { width: 11px; height: 11px; fill: none; stroke: var(--footer-text); stroke-width: 1.6; }
</style>
</head>
<body>
<div class="letterhead">
  <header class="brand">
    <span class="brand-square"></span>
    <span class="brand-name">THORNWELL</span>
  </header>

  <footer>
    <div class="address-band">1876 NE 57th Ave, Portland, OR 97213</div>
    <div class="contact-band">
      <span class="contact-item">
        <svg viewBox="0 0 12 12" aria-label="phone"><path d="M3 1 L5 3.5 L4 5 Q5 7 7 8 L8.5 7 L11 9 L9.5 11 Q4 10.5 1 3 Z"/></svg>
        971 555 0147
      </span>
      <span class="contact-item">
        <svg viewBox="0 0 12 12" aria-label="fax"><rect x="1.5" y="5" width="9" height="5"/><rect x="3.5" y="1.5" width="5" height="3.5"/></svg>
        971 555 0182
      </span>
      <span class="contact-item">
        <svg viewBox="0 0 12 12" aria-label="email"><rect x="1" y="3" width="10" height="7"/><path d="M1 3 L6 7 L11 3"/></svg>
        info@thornwell-law.com
      </span>
      <span class="contact-item">
        <svg viewBox="0 0 12 12" aria-label="website"><circle cx="6" cy="6" r="4.8"/><ellipse cx="6" cy="6" rx="2" ry="4.8"/><path d="M1.2 6 H10.8"/></svg>
        www.thornwell-law.com
      </span>
    </div>
  </footer>
</div>
</body>
</html>
```